Redesign Merle's RV Park & Lodge Website, Leeds, North Dakota

I need a totally re-designed website for my RV Park / Lodge. I want to not only provide information on my RV Park / Lodge, I want to provide my customers with information on the town and area attractions. I want to provide rate information. Ideally, I would like to have a button/page for each section: Welcome & Information, Area Attractions, Welcome to Leeds, Rates, Who's Merle?!, FAQ's and Where are we?. I don't know if this would be more expensive the more pages you have? If more pages is too expensive, then we can combine info on less pages. I want my logo included on the web page. I want Studio Flock to take down my old website and use the same address to put up my newly designed website.

Target Market(s)

Full time RVers, People who camp, hunt fish, People who recreate on Devils Lake, People who are looking for meeting/conference space, people who are looking for party venue

Industry/Entity Type

Accommodation

Number of Pages Required

3 page

Requirements
Must have
• I want a cozy, welcoming type web site. No super dark colors. Bright and cheerful.
• Must be simple and organized.
• NOTE: I have a file of pictures of the interior of Merle's Lodge that must be included in website. Please request this file if you will be designing my project as the files are too large to upload through Studio Flock.
Nice to have
• If you cannot open any of the files listed, please notify me.
Should not have
• No stark or super-formal designs.

```html
<!DOCTYPE html>
<html lang="en">
<head>
<meta charset="utf-8">
<title>Merle's RV Park &amp; Lodge – Leeds, North Dakota</title>
<link rel="stylesheet" href="https://fonts.googleapis.com/css2?family=Roboto+Condensed:wght@400;700&family=Open+Sans:wght@400;600&display=swap">
<style>
:root{
  --red:#c8102e;
  --green-dark:#3f5a26;
  --green:#5f7b3e;
  --green-light:#7c9658;
  --ink:#1e1e1e;
  --body:#444;
  --line:#cfcfcf;
  --footer:#111;
  --footer-bottom:#080808;
  --white:#fff;
}
*{box-sizing:border-box;margin:0;padding:0}
html,body{width:1200px;height:3358px;overflow:hidden}
body{position:relative;background:var(--white);font-family:"Open Sans",Arial,sans-serif;color:var(--body)}
.abs{position:absolute}
h2,h3,.cond{font-family:"Roboto Condensed","Arial Narrow",sans-serif;font-weight:400;color:var(--ink)}

/* header */
.site-header{left:0;top:0;width:1200px;height:130px}
.brand{left:92px;top:22px;display:flex;align-items:center;gap:14px}
.brand-mark{width:46px;height:46px;background:var(--green-dark)}
.brand-name{font-family:"Roboto Condensed",sans-serif;font-weight:700;font-size:20px;line-height:22px;color:var(--ink);width:140px}
.contact{display:flex;align-items:center;gap:14px;font-size:16px;color:var(--ink)}
.contact small{display:block;font-size:18px;margin-bottom:2px}
.icon-ring{width:48px;height:48px;border:2px solid #555;border-radius:50%;display:flex;align-items:center;justify-content:center}
.contact-phone{left:496px;top:37px}
.contact-email{left:712px;top:37px}
.login{left:1018px;top:45px;width:92px;height:36px;border-radius:18px;background:var(--red);color:var(--white);font-size:17px;display:flex;align-items:center;justify-content:center}

/* nav */
.main-nav{left:0;top:130px;width:1200px;height:50px;background:linear-gradient(180deg,var(--green-light),var(--green-dark));display:flex;padding-left:90px}
.main-nav a{color:var(--white);text-decoration:none;font-size:15px;padding:0 16px;display:flex;align-items:center}
.main-nav a.active{background:var(--red);padding:0 24px}

/* hero */
.hero{left:0;top:180px;width:1200px;height:502px;background:linear-gradient(180deg,#cfe2f4 0%,#e9eef3 38%,#9e9e9e 39%,#7d2630 48%,#8a8a8a 60%,#8fae5c 70%,#b9a98a 100%)}
.hero-title{right:88px;top:345px;text-align:right;color:var(--white);text-shadow:0 2px 4px rgba(0,0,0,.45)}
.hero-title h1{font-family:"Roboto Condensed",sans-serif;font-weight:700;font-size:56px;line-height:60px;letter-spacing:1px}
.hero-title p{font-family:"Open Sans",sans-serif;font-size:30px;color:#f2f2f2}
.hero-arrows{left:92px;top:612px;display:flex;gap:6px}
.hero-arrows span{width:22px;height:22px;border-radius:50%;background:rgba(0,0,0,.55);display:flex;align-items:center;justify-content:center}

/* welcome */
.welcome{left:0;top:770px;width:1200px;text-align:center}
.welcome h2{font-size:34px;margin-bottom:22px}
.welcome p{width:1060px;margin:0 auto;font-size:15px;line-height:27px;color:#333}
.card{top:936px;width:428px;height:322px;background:var(--white);box-shadow:0 2px 8px rgba(0,0,0,.25)}
.card-img{height:195px}
.card h3{font-size:21px;text-align:center;margin:24px 0 10px}
.card p{font-size:13px;line-height:22px;text-align:center;padding:0 40px;color:#333}
.card-lodge{left:152px}
.card-meeting{left:616px}

/* feature rows */
.feature-box{background:var(--white);border:1px solid #8f8f8f;padding:40px 36px}
.feature-box h2{font-family:"Open Sans",sans-serif;font-size:34px;font-weight:400;margin-bottom:18px}
.feature-box h2.cond{font-family:"Roboto Condensed",sans-serif}
.feature-box ul{list-style:none}
.feature-box li{font-size:15px;line-height:26px;color:#333;padding-left:20px;position:relative}
.feature-box li::before{content:"»";position:absolute;left:0;top:-1px;color:var(--red);font-weight:600}
.btn-more{display:inline-flex;align-items:center;justify-content:center;background:var(--red);color:var(--white);font-size:12px;height:34px;padding:0 20px;border-radius:17px;margin-top:16px;text-transform:uppercase}
.lodge-img{left:0;top:1359px;width:602px;height:484px;background:linear-gradient(180deg,#8a9aa8 0%,#5e6f58 38%,#2f5f7e 50%,#7a4a3a 70%,#58663c 100%)}
.lodge-box{left:602px;top:1359px;width:479px;height:484px}
.rv-box{left:123px;top:1843px;width:479px;height:486px}
.rv-img{left:602px;top:1843px;width:598px;height:486px;background:linear-gradient(180deg,#6f93c4 0%,#e3ecf4 30%,#8e8a7e 48%,#7a9c4e 70%,#9b4a32 82%,#6e9640 100%)}

/* tents */
.tent-img{left:112px;top:2430px;width:398px;height:279px;background:radial-gradient(ellipse at 50% 55%,#e0a81c 0%,#d59a18 35%,#2a47a0 65%,#fff 67%)}
.tents{left:544px;top:2425px;width:542px}
.tents h2{font-size:38px;margin-bottom:14px}
.tents p{font-size:13.5px;line-height:24px;color:#333;text-align:justify}

/* testimonials */
.reviews{left:0;top:2799px;width:1200px;height:219px;background:radial-gradient(ellipse at 50% 50%,var(--green-light) 0%,var(--green) 45%,var(--green-dark) 100%);text-align:center;padding-top:66px}
.reviews h2{color:var(--white);font-size:30px;margin-bottom:28px}
.reviews a{display:inline-flex;align-items:center;justify-content:center;width:126px;height:36px;border:1px solid var(--white);border-radius:18px;color:var(--white);text-decoration:none;font-size:17px}

/* footer */
.site-footer{left:0;top:3018px;width:1200px;height:262px;background:var(--footer);color:var(--white)}
.footer-brand{left:92px;top:112px;display:flex;align-items:center;gap:12px}
.footer-brand .brand-name{color:var(--white);font-size:17px;line-height:19px;width:120px}
.footer-brand .brand-mark{width:40px;height:40px;background:var(--green)}
.footer-col h4{font-weight:400;font-size:14px;letter-spacing:.3px;margin-bottom:20px;text-transform:uppercase}
.footer-col li{list-style:none;font-size:13px;display:flex;align-items:center;gap:12px;margin-bottom:14px}
.col-contact{left:366px;top:78px}
.col-news{left:667px;top:78px;width:210px}
.col-news p{font-size:12px;line-height:16px;margin-bottom:12px}
.news-form{display:flex}
.news-form span{width:145px;height:30px;background:var(--white);color:#888;font-size:11px;display:flex;align-items:center;padding-left:8px}
.news-form b{width:58px;height:30px;background:var(--red);font-weight:400;font-size:13px;display:flex;align-items:center;justify-content:center}
.col-social{left:942px;top:78px}
.social{display:flex;gap:10px}
.social span{width:26px;height:26px;background:var(--white);border-radius:3px}
.footer-bottom{left:0;top:3280px;width:1200px;height:78px;background:var(--footer-bottom);color:var(--white);font-size:13px;display:flex;align-items:center;justify-content:center}
</style>
</head>
<body>

<header class="site-header abs">
  <div class="brand abs">
    <span class="brand-mark"></span>
    <span class="brand-name">Merle's RV Park &amp; Lodge Leeds ND</span>
  </div>
  <div class="contact contact-phone abs">
    <span class="icon-ring"><svg width="20" height="20" viewBox="0 0 24 24"><path d="M6.6 10.8a15 15 0 0 0 6.6 6.6l2.2-2.2a1 1 0 0 1 1-.25 11.4 11.4 0 0 0 3.6.6 1 1 0 0 1 1 1V20a1 1 0 0 1-1 1A17 17 0 0 1 3 4a1 1 0 0 1 1-1h3.5a1 1 0 0 1 1 1c0 1.25.2 2.45.6 3.6a1 1 0 0 1-.25 1z" fill="#444"/></svg></span>
    <div><small>Phone</small>701-555-0148</div>
  </div>
  <div class="contact contact-email abs">
    <span class="icon-ring"><svg width="22" height="22" viewBox="0 0 24 24"><circle cx="12" cy="12" r="11" fill="#444"/><path d="M6 8h12v8H6z" fill="#fff"/><path d="M6 8l6 5 6-5" stroke="#444" stroke-width="1.4" fill="none"/></svg></span>
    <div><small>Email</small>stay@merlesrvlodge.com</div>
  </div>
  <a class="login abs">Login</a>
</header>

<nav class="main-nav abs">
  <a class="active">Home</a>
  <a>Welcome &amp; Information</a>
  <a>Area Attractions</a>
  <a>Welcome to Leeds</a>
  <a>Rates</a>
  <a>Who's Merle?!</a>
  <a>FAQ's</a>
  <a>Where are we</a>
</nav>

<section class="hero abs" role="img" aria-label="Photo of the red-roofed lodge building on the prairie under a bright sky"></section>
<div class="hero-title abs">
  <h1>MERLE'S RV PARK &amp; LODGE</h1>
  <p>Porro quisquam est qui dolorem</p>
</div>
<div class="hero-arrows abs">
  <span><svg width="10" height="10" viewBox="0 0 10 10"><path d="M7 1L3 5l4 4" stroke="#fff" stroke-width="2" fill="none"/></svg></span>
  <span><svg width="10" height="10" viewBox="0 0 10 10"><path d="M3 1l4 4-4 4" stroke="#fff" stroke-width="2" fill="none"/></svg></span>
</div>

<section class="welcome abs">
  <h2>Welcome to Merle's RV Park &amp; Lodge and Leeds, North Dakota</h2>
  <p>Leeds is in the heart of some of the greatest hunting and fishing in the world. Merle&amp; RV Park is located right on Highway 2 midway between Devils Lake and Rugby North Dakota. We are smack dab in the middle of it all!</p>
</section>

<article class="card card-lodge abs">
  <div class="card-img" role="img" aria-label="Photo of a guest sitting on a blue tractor" style="background:linear-gradient(180deg,#3a4fa0 0%,#2a3b82 55%,#1d2a5c 100%)"></div>
  <h3>Merle's Lodge</h3>
  <p>Are you looking for a cozy, but spacious home away from home? Well, you have found it! Merle's Lodge is 2200</p>
</article>
<article class="card card-meeting abs">
  <div class="card-img" role="img" aria-label="Photo of the meeting room set with tables and chairs" style="background:linear-gradient(180deg,#8a3a3a 0%,#c9b9a4 45%,#e8e4de 100%)"></div>
  <h3>Meeting / Conference Space</h3>
  <p>Are you looking for a venue for your next meeting, training event, guys/girls weekend, quilt retreat, holiday</p>
</article>

<div class="lodge-img abs" role="img" aria-label="Photo of a large timber lodge by a mountain lake"></div>
<section class="feature-box lodge-box abs">
  <h2>MERLE'S LODGE</h2>
  <ul>
    <li>Groups – hunting, fishing, working, playing</li>
    <li>2200 square feet</li>
    <li>Full kitchen</li>
    <li>Free WiFi</li>
    <li>Satellite TV</li>
    <li>2 restrooms, one is handicap accessible</li>
    <li>Sleeps 14 – 2 bedrooms with queen sized beds, plus a shared sleeping area with bunk beds</li>
    <li>A great room with ample seating for large groups</li>
    <li>Merle's supplies everything...bedding, towels, cookware,</li>
    <li>Kids stay free.</li>
  </ul>
  <span class="btn-more">Read more</span>
</section>

<section class="feature-box rv-box abs">
  <h2 class="cond">Merle's RV PARK</h2>
  <ul>
    <li>Electric (23, 30 &amp;amp; 50amp), Water, Sewer</li>
    <li>Free WiFi</li>
    <li>Safe &amp;amp; convenient location</li>
    <li>24 hour indoor restroom with shower</li>
    <li>Open Road Club accepted for first night</li>
    <li>Ample room to park boats, trailers etc.</li>
    <li>Convenience store/gas station located right across the street. Restaurant onsite.</li>
    <li>Merle's operates on a first come, first serve basis for short term stays. If you would like to reserve for a stay longer than 3 days, please call Merle.</li>
  </ul>
  <span class="btn-more">Read more</span>
</section>
<div class="rv-img abs" role="img" aria-label="Photo of a red log cabin in a green valley below snowy mountains"></div>

<div class="tent-img abs" role="img" aria-label="Photo of a yellow and blue dome tent"></div>
<section class="tents abs">
  <h2>TENTS</h2>
  <p>Are you looking for a venue for your next meeting, training event, guys/girls weekend, quilt retreat, holiday gathering, family reunion, birthday, wedding party or get-together? We've got you covered! Merle's Lodge seats about 65 people comfortably. Many of our customers have commented that Merle's was the perfect place for their event because it was so inviting...and just like home! Are you looking for a cozy, but spacious home away from home? Well, you have found it! Merle'sLodge is 2200 square feet of living space.</p>
  <span class="btn-more">Read more</span>
</section>

<section class="reviews abs">
  <h2>Find out what our customers are saying about Merle's RV Park &amp;Lodge.</h2>
  <a>Click Here</a>
</section>

<footer class="site-footer abs">
  <div class="footer-brand abs">
    <span class="brand-mark"></span>
    <span class="brand-name">Merle's RV Park &amp; Lodge Leeds ND</span>
  </div>
  <div class="footer-col col-contact abs">
    <h4>Contact us</h4>
    <ul>
      <li><svg width="12" height="16" viewBox="0 0 12 16"><path d="M6 0a6 6 0 0 1 6 6c0 4.5-6 10-6 10S0 10.5 0 6a6 6 0 0 1 6-6z" fill="#fff"/><circle cx="6" cy="6" r="2.2" fill="#111"/></svg>120 Prairie Ave Leeds ND 58000</li>
      <li><svg width="14" height="14" viewBox="0 0 24 24"><path d="M6.6 10.8a15 15 0 0 0 6.6 6.6l2.2-2.2a1 1 0 0 1 1-.25 11.4 11.4 0 0 0 3.6.6 1 1 0 0 1 1 1V20a1 1 0 0 1-1 1A17 17 0 0 1 3 4a1 1 0 0 1 1-1h3.5a1 1 0 0 1 1 1c0 1.25.2 2.45.6 3.6a1 1 0 0 1-.25 1z" fill="#fff"/></svg>701-555-0148, 701-555-0192</li>
      <li><svg width="14" height="12" viewBox="0 0 14 12"><rect width="14" height="12" fill="#fff"/><path d="M0 1l7 5 7-5" stroke="#111" stroke-width="1.4" fill="none"/></svg>stay@merlesrvlodge.com</li>
    </ul>
  </div>
  <div class="footer-col col-news abs">
    <h4>Sign up for newsletter</h4>
    <p>Your about us information would fit here nicely.</p>
    <div class="news-form"><span>Email address</span><b>Submit</b></div>
  </div>
  <div class="footer-col col-social abs">
    <h4>Follow us out there</h4>
    <div class="social"><span></span><span></span><span></span><span></span></div>
  </div>
</footer>
<div class="footer-bottom abs">Copyright © 2018. All Rights Reserved</div>

</body>
</html>
```